Moridel SA

Découpe de métaux - Fourniture de tôles - Accessoires de machines de chantier (European Patent)

Les designs se ressemblent

Besoin de plus de jours pour examiner

• Mon projet doit comprendre la photo de la halle (bâtiment)

```html
<!DOCTYPE html>
<html lang="fr">
<head>
<meta charset="utf-8">
<title>Moridel SA – Annonce</title>
<link href="https://fonts.googleapis.com/css2?family=Oswald:wght@400;500;600;700&display=swap" rel="stylesheet">
<style>
  :root {
    --page-bg: #5c5c5e;
    --ink-dark: #29282d;
    --ink-darker: #1f1e23;
    --paper: #f4f4f4;
    --paper-shade: #d9d9db;
    --white: #ffffff;
    --text-dark: #222226;
    --brand-red: #d8262c;
    --photo-sky: #5f7f9e;
    --photo-steel: #7b7890;
    --photo-glow: #b9a8d9;
  }
  * { box-sizing: border-box; margin: 0; padding: 0; }
  html, body {
    width: 1200px; height: 617px; overflow: hidden;
    background: var(--page-bg);
    font-family: "Oswald", "Arial Narrow", sans-serif;
  }
  .stage { position: relative; width: 1200px; height: 617px; }
  .poster {
    position: absolute; left: 398px; top: 23px;
    width: 753px; height: 1065px;
    transform: scale(0.535); transform-origin: 0 0;
    background: var(--ink-dark);
    overflow: hidden;
    box-shadow: 0 20px 40px rgba(0,0,0,.45);
  }
  .poster-shapes, .site-photo { position: absolute; left: 0; top: 0; }
  .brand-name {
    position: absolute; left: 72px; top: 78px;
    display: flex; align-items: center; gap: 16px;
    color: var(--white); font-weight: 600; font-size: 52px; line-height: 1; white-space: nowrap;
  }
  .brand-dot { width: 34px; height: 34px; border-radius: 50%; background: var(--brand-red); }
  .contact-chip {
    position: absolute; height: 44px;
    background: var(--white); color: var(--text-dark);
    display: flex; align-items: center; justify-content: center; gap: 10px;
    font-size: 25px; font-weight: 400; line-height: 1; white-space: nowrap;
  }
  .contact-chip svg { width: 22px; height: 22px; flex: none; }
  .chip-web { left: 451px; top: 52px; width: 245px; }
  .chip-mail { left: 451px; top: 927px; width: 245px; }
  .service-list { position: absolute; left: 102px; top: 670px; }
  .service {
    border-left: 2px solid var(--text-dark);
    padding-left: 18px; margin-bottom: 26px;
    color: var(--text-dark); font-weight: 500; font-size: 44px; line-height: 1.08;
    text-transform: uppercase; white-space: nowrap;
  }
  .patent-offer { position: absolute; left: 424px; top: 660px; width: 260px; color: var(--text-dark); }
  .patent-offer h2 {
    font-weight: 500; font-size: 44px; line-height: 1.08; text-transform: uppercase;
    border-bottom: 2px solid var(--text-dark); padding-bottom: 8px; width: 234px;
  }
  .patent-offer p { font-size: 29px; font-weight: 400; margin-top: 12px; white-space: nowrap; }
  .call-line {
    position: absolute; left: 48px; top: 990px; width: 660px;
    display: flex; align-items: center; justify-content: space-between;
    color: var(--white); font-weight: 600; font-size: 52px; line-height: 1;
    white-space: nowrap;
  }
  .call-line svg { width: 48px; height: 48px; flex: none; }
</style>
</head>
<body>
<main class="stage">
  <article class="poster">
    <svg class="poster-shapes" width="753" height="1065" aria-hidden="true">
      <polygon points="0,655 753,560 753,870 0,955" fill="var(--paper)"/>
      <polygon points="0,780 360,955 0,955" fill="var(--paper-shade)"/>
    </svg>
    <svg class="site-photo" width="753" height="1065" role="img" aria-label="Photo d'une tête de découpe plasma au travail, à côté de la halle de l'entreprise sous un ciel de montagne">
      <defs>
        <linearGradient id="photoTone" x1="0" y1="0" x2="1" y2="1">
          <stop offset="0" stop-color="var(--photo-steel)"/>
          <stop offset=".45" stop-color="var(--photo-glow)"/>
          <stop offset=".7" stop-color="var(--photo-sky)"/>
          <stop offset="1" stop-color="#5a6e4a"/>
        </linearGradient>
      </defs>
      <polygon points="0,225 753,150 753,560 0,655" fill="url(#photoTone)"/>
    </svg>

    <div class="brand-name"><span class="brand-dot"></span>Moridel SA</div>

    <div class="contact-chip chip-web">
      <svg viewBox="0 0 24 24" fill="none" stroke="currentColor" stroke-width="1.6"><circle cx="12" cy="12" r="9"/><ellipse cx="12" cy="12" rx="4" ry="9"/><line x1="3" y1="12" x2="21" y2="12"/></svg>
      WWW.MORIDEL.CH
    </div>

    <div class="service-list">
      <p class="service">Découpe<br>de métaux</p>
      <p class="service">Fourniture<br>de tôles</p>
    </div>

    <div class="patent-offer">
      <h2>Accessoires de machines de chantier</h2>
      <p>(European Patent)</p>
    </div>

    <div class="contact-chip chip-mail">
      <svg viewBox="0 0 24 24" fill="none" stroke="currentColor" stroke-width="1.6"><rect x="3" y="6" width="18" height="12"/><polyline points="3,6 12,13 21,6"/></svg>
      INFO@MORIDEL.CH
    </div>

    <div class="call-line">
      <span class="call-label">CALL US NOW</span>
      <svg viewBox="0 0 24 24" fill="none" stroke="currentColor" stroke-width="1.8"><circle cx="12" cy="12" r="10"/><path d="M9 7c-1 1-1.5 2 0 5s3 4.5 5 5c1 .3 2-.5 2.3-1l-1.8-1.7-1.3.8c-1-.5-2.3-1.8-2.8-2.8l.8-1.3L9.5 6.6z" fill="currentColor" stroke="none"/></svg>
      <span class="call-number">027/555.41.68</span>
    </div>
  </article>
</main>
</body>
</html>
```